Velvet Riot Rising Line of Sparkling Wine & Spirits

Back info: Nora Beth Quill Owner 555-318-4402 1480 E. Harlow Ave, Bldg. 2, & 3, Fenwick Bay 95871
Sparkling Wines & Memorabilia www.velvetriotrising.com
Ok I have uploaded the winning design. The color that I am after is the Fushia, Raspberry, Red, Matte Satin Matalic Finish. With a 24 Karet Gold color Foil. The Bottle is on the top row and it's the 2nd Bottle in. That is the Color that I want. This is the style of font. Make sure that you put what we're advertising. Good Luck to you all. Warmest regards, Nora
21 & up UniSex
Sparkling Wine and Memorabilia
there listed up above.....

```html
<!DOCTYPE html>
<html lang="en">
<head>
<meta charset="utf-8">
<title>Velvet Riot Rising – Business Card</title>
<link href="https://fonts.googleapis.com/css2?family=Arimo:wght@400;700&display=swap" rel="stylesheet">
<style>
  :root {
    --backdrop: #e4e4e4;
    --card-dark: #353535;
    --card-dark-top: #414141;
    --fuchsia: #e2127e;
    --fuchsia-deep: #a80c5c;
    --gold: #e9cf73;
    --text-light: #ffffff;
    --ink: #1c1c1c;
    --grey-fade: #8a8a8a;
  }
  * { margin: 0; padding: 0; box-sizing: border-box; }
  html, body { width: 1200px; height: 1200px; overflow: hidden; }
  body {
    background: var(--backdrop);
    font-family: "Arimo", Arial, sans-serif;
    position: relative;
  }
  .card {
    position: absolute;
    left: 256px;
    width: 688px;
    height: 394px;
  }
  .card-front {
    top: 150px;
    background: linear-gradient(to bottom, var(--card-dark-top), var(--card-dark));
  }
  .card-back {
    top: 652px;
    background: linear-gradient(to bottom, #ffffff 0%, #ffffff 47%, #c9c9c9 68%, var(--grey-fade) 100%);
  }
  .bottle-art {
    position: absolute;
    background: linear-gradient(to bottom, var(--fuchsia-deep) 0%, var(--fuchsia-deep) 20%, var(--gold) 20%, var(--gold) 24%, var(--fuchsia) 24%, var(--fuchsia-deep) 100%);
    border-radius: 8px 8px 6px 6px;
  }
  .card-front .bottle-art { left: 43px; top: 28px; width: 50px; height: 163px; }
  .card-back .bottle-art { left: 309px; top: 57px; width: 70px; height: 242px; }
  .owner-name {
    position: absolute; left: 44px; top: 208px;
    color: var(--fuchsia);
    font-weight: 700; font-size: 28px; letter-spacing: 0.2px;
  }
  .owner-title {
    position: absolute; left: 44px; top: 242px;
    color: var(--gold); font-size: 19px;
  }
  .address {
    position: absolute; left: 44px; top: 276px;
    color: var(--text-light); font-size: 17px; line-height: 22px;
  }
  .contact {
    position: absolute; left: 44px; top: 330px;
    color: var(--text-light); font-size: 17px; line-height: 21px;
    list-style: none;
  }
  .contact li { display: flex; align-items: center; gap: 12px; }
  .contact svg { width: 14px; height: 14px; flex: none; }
  .shelf-line {
    position: absolute; left: 150px; top: 299px; width: 388px; height: 1px;
    background: linear-gradient(to right, transparent, #3a3a3a 50%, transparent);
  }
  .tagline {
    position: absolute; left: 0; right: 0; top: 326px;
    text-align: center; color: var(--ink);
    font-size: 17px; letter-spacing: 4px;
  }
  .tagline strong { font-weight: 700; }
</style>
</head>
<body>
  <section class="card card-front">
    <div class="bottle-art" role="img" aria-label="Illustration of a fuchsia Velvet Riot Rising sparkling wine bottle with gold foil"></div>
    <h1 class="owner-name">NORA BETH QUILL</h1>
    <p class="owner-title">Owner</p>
    <p class="address">E. Harlow Ave<br>Bldg. 2, &amp; 3, Fenwick Bay 95871</p>
    <ul class="contact">
      <li>
        <svg viewBox="0 0 24 24" aria-hidden="true"><path fill="#e2127e" d="M6.6 10.8a15.1 15.1 0 0 0 6.6 6.6l2.2-2.2a1 1 0 0 1 1-.25 11.4 11.4 0 0 0 3.6.57 1 1 0 0 1 1 1V20a1 1 0 0 1-1 1A17 17 0 0 1 3 4a1 1 0 0 1 1-1h3.5a1 1 0 0 1 1 1c0 1.25.2 2.45.57 3.57a1 1 0 0 1-.25 1z"/></svg>
        555-318-4402 1480
      </li>
      <li>
        <svg viewBox="0 0 24 24" aria-hidden="true"><circle cx="12" cy="12" r="10" fill="#e2127e"/><path fill="#353535" d="M7 6c2 1 3 3 2 5s-3 1-3 4c0 1 1 2 1 3A8 8 0 0 1 7 6zm7 3c2-1 4 0 4 2s-2 2-2 4-2 3-3 2 0-3-1-4 0-3 2-4z"/></svg>
        www.velvetriotrising.com
      </li>
    </ul>
  </section>

  <section class="card card-back">
    <div class="bottle-art" role="img" aria-label="Illustration of a fuchsia Velvet Riot Rising sparkling wine bottle with gold foil"></div>
    <div class="shelf-line"></div>
    <p class="tagline">SPARKLING <strong>WINES &amp; MEMORABILIA</strong></p>
  </section>
</body>
</html>
```